Parcelwise HQ letterhead and envelope

Design a formal (8.5x11) letterhead and envelope for sales outreach and legal matters. Using design input from https://www.parcelwisehq.example/ and the attached documents.

Industry/Entity Type

Software Service

Requirements
Must have
• These 4 hex colors are our official colors:
• #355c98 [blue]
• #1eb1a2 [teal]
• #fdba12 [gold]
• #f1653b [orange]
• So no other colors besides these should be used.

```html
<!DOCTYPE html>
<html lang="en">
<head>
<meta charset="utf-8">
<title>Parcelwise HQ Letterhead</title>
<link href="https://fonts.googleapis.com/css2?family=Lato:wght@400;700&family=Arimo:wght@400&family=Dancing+Script:wght@700&display=swap" rel="stylesheet">
<style>
  :root {
    --brand-blue: #355c98;
    --brand-teal: #1eb1a2;
    --paper: #ffffff;
    --ink: #4a4a4a;
    --ink-dark: #2b2b2b;
    --watermark: #e6eaf1;
  }
  html, body {
    margin: 0;
    padding: 0;
    width: 996px;
    height: 1200px;
    overflow: hidden;
    background: var(--paper);
  }
  .letterhead {
    position: relative;
    width: 996px;
    height: 1200px;
    background: linear-gradient(180deg, #ffffff 0%, #fbfbfc 60%, #f6f7f9 100%);
    font-family: "Lato", sans-serif;
    overflow: hidden;
  }
  .brand {
    position: absolute;
    left: 63px;
    top: 38px;
    display: flex;
    align-items: center;
    gap: 14px;
  }
  .brand-dot {
    width: 46px;
    height: 46px;
    border-radius: 50%;
    background: var(--brand-blue);
  }
  .brand-name {
    font-family: "Lato", sans-serif;
    font-weight: 400;
    font-size: 44px;
    color: var(--brand-blue);
    letter-spacing: 0.5px;
  }
  .contact {
    position: absolute;
    left: 697px;
    top: 30px;
    height: 67px;
    border-left: 1.5px solid #c9c9c9;
    padding-left: 12px;
    font-family: "Arimo", sans-serif;
    font-size: 14.5px;
    color: var(--ink-dark);
  }
  .contact-line {
    display: flex;
    align-items: center;
    gap: 6px;
    height: 24.5px;
  }
  .contact-icon { width: 14px; height: 14px; flex: none; }
  .watermark {
    position: absolute;
    left: 560px;
    top: 790px;
    width: 500px;
    height: 500px;
    border-radius: 50%;
    background: var(--watermark);
    opacity: 0.7;
  }
  .letter {
    position: absolute;
    left: 84px;
    top: 264px;
    width: 827px;
    color: var(--ink);
  }
  .salutation {
    margin: 0 0 24px;
    font-weight: 700;
    font-size: 17px;
    color: var(--brand-blue);
  }
  .letter-body p {
    margin: 0 0 22px;
    font-size: 17.5px;
    line-height: 27px;
    text-align: justify;
    hyphens: auto;
  }
  .closing {
    margin: 8px 0 0;
    font-size: 20px;
    color: var(--ink-dark);
  }
  .signature {
    margin: 4px 0 0;
    font-family: "Dancing Script", cursive;
    font-weight: 700;
    font-size: 36px;
    color: var(--brand-blue);
  }
  .address {
    position: absolute;
    left: 64px;
    top: 1151px;
    display: flex;
    align-items: center;
    gap: 5px;
    font-family: "Arimo", sans-serif;
    font-size: 14.5px;
    color: var(--ink-dark);
  }
  .footer-band {
    position: absolute;
    left: 0;
    top: 1150px;
    width: 996px;
    height: 50px;
  }
  .website {
    position: absolute;
    left: 640px;
    width: 356px;
    top: 1173px;
    text-align: center;
    font-family: "Arimo", sans-serif;
    font-size: 18px;
    letter-spacing: 3px;
    color: #ffffff;
  }
</style>
</head>
<body>
<main class="letterhead">
  <header>
    <div class="brand">
      <span class="brand-dot"></span>
      <span class="brand-name">Parcelwise HQ</span>
    </div>
    <address class="contact" style="font-style:normal">
      <div class="contact-line">
        <svg class="contact-icon" viewBox="0 0 14 14"><circle cx="7" cy="7" r="6" fill="none" stroke="#355c98" stroke-width="1.3"/><rect x="4.5" y="4" width="5" height="6" rx="1" fill="none" stroke="#355c98" stroke-width="1.1"/></svg>
        (555) 214-6630
      </div>
      <div class="contact-line">
        <svg class="contact-icon" viewBox="0 0 14 14"><circle cx="7" cy="7" r="6" fill="none" stroke="#355c98" stroke-width="1.3"/><path d="M4.5 4 L6 4 L6.6 5.8 L5.8 6.5 Q6.6 8 7.8 8.6 L8.5 7.8 L10 8.4 L10 9.8 Q6 10 4.2 5.2 Z" fill="#355c98"/></svg>
        (555) 908-4417(Main)
      </div>
      <div class="contact-line">
        <svg class="contact-icon" viewBox="0 0 14 14"><circle cx="7" cy="7" r="6" fill="none" stroke="#355c98" stroke-width="1.3"/><rect x="4" y="5" width="6" height="4.2" fill="none" stroke="#355c98" stroke-width="1"/><path d="M4 5 L7 7.3 L10 5" fill="none" stroke="#355c98" stroke-width="1"/></svg>
        mlane@parcelwisehq.example
      </div>
    </address>
  </header>

  <div class="watermark" role="img" aria-label="Faint brand mark decoration"></div>

  <section class="letter">
    <p class="salutation">Dear Mr. Lorem,</p>
    <div class="letter-body">
      <p>Lorem ipsum dolor sit amet, consectetuer adipiscing elit, sed diam nonummy nibh euismod tincidunt ut laoreet dolore magna aliquam erat volutpat. Ut wisi enim ad minim veniam, quis nostrud exerci tation ullamcorper suscipit lobortis nisl ut aliquip ex ea commodo consequat. Duis autem vel eum iriure dolor in hendiusto odio dignissim qui blandit praesent luptatum zzril delenit augue duis dolore te feugait nulla facilisi.</p>
      <p>Lorem ipsum dolor sit amet, consectetuer adipiscing elit, sed diam nonummy nibh euismod tincidunt ut laoreet dolore magna aliquam erat volutpat. Ut wisi enim ad minim veniam, quis nostrud exerci tation ullamcorper suscipit lobortis nisl ut aliquip ex ea commodo consequat. Duis autem vel eum iriure dolor in hendiusto odio dignissim qui blandit praesent luptatum zzril delenit augue duis dolore te feugait nulla facilisi.</p>
      <p>Lorem ipsum dolor sit amet, consectetuer adipiscing elit, sed diam nonummy nibh euismod tincidunt ut laoreet dolore magna aliquam erat volutpat. Ut wisi enim ad minim veniam, quis nostrud exerci tation ullamcorper suscipit lobortis nisl ut aliquip ex ea commodo consequat. Duis autem vel eum iriure dolor in hendiusto odio dignissim qui blandit praesent luptatum zzril delenit augue duis dolore te feugait nulla facilisi.</p>
    </div>
    <p class="closing">Sincerely Your,</p>
    <p class="signature">Your Name</p>
  </section>

  <footer>
    <svg class="footer-band" viewBox="0 0 996 50" aria-hidden="true">
      <path d="M0 28 H600 Q612 28 618 24 L621 27 Q613 32 600 32 H0 Z" fill="#1eb1a2"/>
      <path d="M0 38 H610 C632 38 628 15 660 15 H996 V50 H0 Z" fill="#355c98"/>
    </svg>
    <div class="address">
      <svg width="14" height="14" viewBox="0 0 14 14" aria-hidden="true"><circle cx="7" cy="7" r="6" fill="none" stroke="#355c98" stroke-width="1.3"/><path d="M7 3.5 A2.4 2.4 0 0 1 9.4 5.9 Q9.4 7.6 7 10.5 Q4.6 7.6 4.6 5.9 A2.4 2.4 0 0 1 7 3.5 Z" fill="#355c98"/><circle cx="7" cy="5.9" r="0.9" fill="#fff"/></svg>
      742 Birch Hollow, Lakeview, MI 48850
    </div>
    <div class="website">www.parcelwisehq.example</div>
  </footer>
</main>
</body>
</html>
```